Stylish Business Cards Wanted

- DOUBLE SIDED Design Required -

High end, edgy cards for a corporate and personal stylist. Must include logo,
Name: Belinda Harwick
Title: Director and Stylist
telephone : +61 8 7142 5809
email: belinda@theloombriefing.example
website: theloombriefing.example
Tag: Corporate Workwear & Uniform Specialist | Personal Stylist
Would like nice icons for telephone, email, website

Target Market(s)

Businesses wanting stylish uniforms, people wanting stylish wardrobes

Industry/Entity Type

Corporate Workwear Stylist

Contact Information for Business Card

I would like black, white and gold foiling incorporated in the design - possibly a touch of the other colours on my branding guide attached Name: Belinda Harwick Title: Director and Stylist telephone : +61 8 7142 5809 email: belinda@theloombriefing.example website: theloombriefing.example Tag: Corporate Workwear & Uniform Specialist | Personal Stylist Would like nice icons for telephone, email, website

Font styles to use
Other font styles liked:
• Raleway

Colors

Designer to choose colors to be used in the design.

Requirements
Must have
• Gold foil accents

```html
<!DOCTYPE html>
<html lang="en">
<head>
<meta charset="utf-8">
<title>The Loom Briefing – Business Cards</title>
<link rel="stylesheet" href="https://fonts.googleapis.com/css2?family=Raleway:wght@400;500;600&family=Lato:wght@400;700&display=swap">
<style>
  :root {
    --backdrop: #1c1c1c;
    --card-white: #ffffff;
    --card-black: #231f20;
    --ink: #1a1a1a;
    --gold: #d4a935;
    --gold-deep: #b08a2e;
    --divider: #9a9a9a;
    --tag-white: #f4f4f4;
  }
  * { box-sizing: border-box; margin: 0; padding: 0; }
  html, body { width: 1200px; height: 900px; overflow: hidden; }
  body {
    background: var(--backdrop);
    font-family: "Lato", Arial, sans-serif;
    display: flex;
    flex-direction: column;
    align-items: center;
    justify-content: space-evenly;
  }
  .card {
    width: 672px;
    height: 384px;
    position: relative;
    border-bottom: 3px solid var(--gold);
    border-left: 3px solid var(--gold);
  }
  .card--front { background: var(--card-white); }
  .card--back { background: var(--card-black); }

  .wordmark {
    font-family: "Raleway", Arial, sans-serif;
    font-weight: 600;
    position: absolute;
    left: 0; right: 0;
    text-align: center;
    white-space: nowrap;
  }
  .card--front .wordmark {
    top: 78px;
    font-size: 34px;
    color: var(--ink);
    letter-spacing: 1px;
  }
  .card--back .wordmark {
    top: 128px;
    font-size: 58px;
    color: var(--gold);
    letter-spacing: 1px;
  }

  .identity {
    position: absolute;
    left: 130px;
    top: 232px;
    display: flex;
    align-items: center;
  }
  .person { text-align: right; padding-right: 22px; }
  .person__name {
    font-size: 24px;
    color: var(--gold);
    letter-spacing: 0.5px;
    text-transform: uppercase;
    line-height: 1.1;
  }
  .person__title {
    font-size: 16px;
    color: var(--ink);
    margin-top: 2px;
  }
  .identity__divider {
    width: 1px;
    height: 66px;
    background: var(--divider);
  }
  .contact {
    list-style: none;
    padding-left: 20px;
    font-family: "Raleway", Arial, sans-serif;
    font-size: 14px;
    color: var(--ink);
  }
  .contact__item {
    display: flex;
    align-items: center;
    gap: 9px;
    line-height: 22px;
  }
  .contact__icon { width: 14px; height: 14px; flex: none; }

  .tagline {
    position: absolute;
    left: 0; right: 0;
    top: 262px;
    text-align: center;
    font-size: 19px;
    color: var(--tag-white);
    letter-spacing: 0.5px;
  }
  .tagline__dot {
    display: inline-block;
    width: 7px; height: 7px;
    border-radius: 50%;
    background: var(--gold);
    margin: 0 12px;
    vertical-align: middle;
  }
</style>
</head>
<body>

  <section class="card card--front" aria-label="Card front">
    <div class="wordmark">The Loom Briefing</div>

    <div class="identity">
      <div class="person">
        <div class="person__name">Belinda Harwick</div>
        <div class="person__title">Director and Stylist</div>
      </div>
      <div class="identity__divider"></div>
      <ul class="contact">
        <li class="contact__item">
          <svg class="contact__icon" viewBox="0 0 24 24" aria-hidden="true">
            <path fill="var(--gold)" d="M6.6 10.8a15.1 15.1 0 0 0 6.6 6.6l2.2-2.2c.3-.3.7-.4 1-.2 1.1.4 2.3.6 3.6.6.6 0 1 .4 1 1V20c0 .6-.4 1-1 1A17 17 0 0 1 3 4c0-.6.4-1 1-1h3.5c.6 0 1 .4 1 1 0 1.3.2 2.5.6 3.6.1.3 0 .7-.2 1z"/>
          </svg>
          <span>+61 8 7142 5809</span>
        </li>
        <li class="contact__item">
          <svg class="contact__icon" viewBox="0 0 24 24" aria-hidden="true">
            <rect x="2" y="5" width="20" height="14" fill="var(--gold)"/>
            <path d="M2 5l10 8 10-8" fill="none" stroke="var(--card-white)" stroke-width="1.6"/>
          </svg>
          <span>belinda@theloombriefing.example</span>
        </li>
        <li class="contact__item">
          <svg class="contact__icon" viewBox="0 0 24 24" aria-hidden="true">
            <circle cx="12" cy="12" r="10" fill="var(--gold)"/>
            <g fill="none" stroke="var(--card-white)" stroke-width="1.2">
              <ellipse cx="12" cy="12" rx="4.5" ry="10"/>
              <path d="M2 12h20M4 7h16M4 17h16"/>
            </g>
          </svg>
          <span>theloombriefing.example</span>
        </li>
      </ul>
    </div>
  </section>

  <section class="card card--back" aria-label="Card back">
    <div class="wordmark">The Loom Briefing</div>
    <p class="tagline">Corporate Workwear &amp; Uniform Specialist<span class="tagline__dot"></span>Personal Stylist</p>
  </section>

</body>
</html>
```